Building company buisness cards

We are looking for a sharp modern new look for our business cards.
We are a New Zealand based company that specialises in house and land packages.
We have attached a photo of the current logo and would like to see if it can be improved somehow if needed.
We are open to any colours but we have chosen green at this stage.
Feel free to change the font and make the logo smarter looking.
Play with the colours and see what looks best.

We want a card that looks so good know one will want to throw it away!

Target Market(s)

Home buyers

Industry/Entity Type

Building

Contact Information for Business Card

Derek Tolvane
0217394062
dtolvane@quillmarkhomesteads.co.nz
quillmarkhomesteads.co.nz

Font styles to use
Serif
Sans Serif

Colors

Designer to choose colors to be used in the design.

Requirements
Must have
• Logo and company name on one side, details on the other side
Nice to have
• Color codes for the original green are HEX #4a8028, RGB(74,128,40), CMYK(42,0,69,50)
• Round corners, Raised and/or spot UV

```html
<!DOCTYPE html>
<html lang="en">
<head>
<meta charset="utf-8">
<title>Quillmark Homesteads – Business Cards</title>
<link rel="stylesheet" href="https://fonts.googleapis.com/css2?family=Open+Sans:wght@400;600;800&display=swap">
<style>
  :root {
    --brand-green: #4a8028;
    --accent-green: #3f8a1f;
    --card-white: #ffffff;
    --card-black: #0d0d0d;
    --text-dark: #333333;
    --backdrop: #e6e3e0;
    --rule-grey: #bdbdbd;
    --rule-dark: #333333;
  }
  * { box-sizing: border-box; margin: 0; padding: 0; }
  html, body {
    width: 1200px; height: 997px; overflow: hidden;
    background: var(--backdrop);
    font-family: "Open Sans", Arial, sans-serif;
  }
  .canvas { position: relative; width: 1200px; height: 997px; }

  .card {
    position: absolute; left: 290px;
    width: 620px; height: 354px;
    border-radius: 10px;
    box-shadow: 0 8px 24px rgba(0,0,0,0.12);
    overflow: hidden;
  }
  .card--front { top: 110px; background: var(--card-white); }
  .card--back  { top: 534px; background: var(--card-black); }

  /* Company name set in the card's text font */
  .company {
    position: absolute;
    display: flex; align-items: center; gap: 10px;
    color: var(--brand-green);
    font-weight: 600;
    line-height: 1;
    white-space: nowrap;
  }
  .company__dot {
    width: 14px; height: 14px; border-radius: 50%;
    background: var(--brand-green); flex: none;
  }
  .company__rule { position: absolute; height: 1px; }

  .card--front .company { right: 40px; top: 78px; font-size: 26px; }
  .card--front .company__rule {
    right: 90px; top: 132px; width: 120px; background: var(--rule-grey);
  }

  .card--back .company {
    left: 0; right: 0; top: 158px; justify-content: center; font-size: 36px;
  }
  .card--back .company__dot { width: 18px; height: 18px; }
  .card--back .company__rule {
    left: 250px; top: 236px; width: 120px; background: var(--rule-dark);
  }

  .accent-block {
    position: absolute; left: 44px;
    border-left: 7px solid var(--accent-green);
    padding-left: 16px;
  }
  .identity { top: 172px; }
  .identity__name {
    color: var(--brand-green); font-weight: 800; font-size: 19px; line-height: 1.15;
  }
  .identity__role {
    color: var(--brand-green); font-weight: 600; font-size: 15px; line-height: 1.2;
  }
  .contact { top: 258px; }
  .contact__line {
    display: flex; align-items: center; gap: 8px;
    color: var(--text-dark); font-size: 15px; line-height: 22px;
  }
  .contact__icon { width: 13px; height: 13px; fill: var(--text-dark); flex: none; }
</style>
</head>
<body>
<main class="canvas">
  <section class="card card--front" aria-label="Business card front">
    <div class="company"><span class="company__dot"></span>Quillmark Homesteads</div>
    <div class="company__rule"></div>

    <div class="accent-block identity">
      <p class="identity__name">Derek Tolvane</p>
      <p class="identity__role">President</p>
    </div>

    <div class="accent-block contact">
      <p class="contact__line">
        <svg class="contact__icon" viewBox="0 0 24 24" aria-hidden="true"><path d="M6.6 10.8a15.1 15.1 0 0 0 6.6 6.6l2.2-2.2a1 1 0 0 1 1-.25 11.4 11.4 0 0 0 3.6.57 1 1 0 0 1 1 1V20a1 1 0 0 1-1 1A17 17 0 0 1 3 4a1 1 0 0 1 1-1h3.5a1 1 0 0 1 1 1c0 1.25.2 2.45.57 3.6a1 1 0 0 1-.25 1z"/></svg>
        0217394062
      </p>
      <p class="contact__line">
        <svg class="contact__icon" viewBox="0 0 24 24" aria-hidden="true"><path d="M2 5h20v14H2z M2 5l10 8 10-8" fill="none" stroke="#333" stroke-width="2.4"/></svg>
        dtolvane@quillmarkhomesteads.co.nz
      </p>
      <p class="contact__line">
        <svg class="contact__icon" viewBox="0 0 24 24" aria-hidden="true"><circle cx="12" cy="12" r="10" fill="none" stroke="#333" stroke-width="2.2"/><path d="M2 12h20M12 2c3 3 3 17 0 20M12 2c-3 3-3 17 0 20" fill="none" stroke="#333" stroke-width="1.8"/></svg>
        www.quillmarkhomesteads.co.nz
      </p>
    </div>
  </section>

  <section class="card card--back" aria-label="Business card back">
    <div class="company"><span class="company__dot"></span>Quillmark Homesteads</div>
    <div class="company__rule"></div>
  </section>
</main>
</body>
</html>
```